Business Card for Coastal Tundrabridge Advisory

We need a business card for Coastal Tundrabridge Advisory. The company website address is provided below. The company logo is attached. We provide specialized permafrost services to the mining, transportation, and oil & gas industries. The card should be prepared for:
Matthias Korhonen, PhD.
Coastal Tundrabridge Advisory
PO Box 418259
Quillwater, Alaska 99642
Direct: +1-907-555-0143
Email: mkorhonen@tundrabridgeadvisory.example
Website: www.coastaltundrabridgeadvisory.example

```html
<!DOCTYPE html>
<html lang="en">
<head>
<meta charset="utf-8">
<title>Coastal Tundrabridge Advisory – Business Card</title>
<link href="https://fonts.googleapis.com/css2?family=Roboto+Condensed:wght@400;700&display=swap" rel="stylesheet">
<style>
  :root {
    --page-bg: #eeeeee;
    --card-white: #ffffff;
    --panel-grey: #868686;
    --ink-black: #111111;
    --ink-white: #ffffff;
    --ink-soft: #f2f2f2;
    --back-dark: #333333;
    --back-mark: #161616;
    --icon-bar: #1e1e1e;
  }
  * { margin: 0; padding: 0; box-sizing: border-box; }
  html, body {
    width: 1199px; height: 1200px; overflow: hidden;
    background: var(--page-bg);
    font-family: "Roboto Condensed", "Arial Narrow", sans-serif;
  }
  .card {
    position: absolute; left: 235px; width: 725px; height: 414px;
    border-radius: 28px; overflow: hidden;
  }
  .card-front { top: 152px; background: var(--card-white); }
  .card-back { top: 649px; background: var(--back-dark); }

  .front-panels { position: absolute; inset: 0; }

  .brand-name {
    position: absolute; left: 40px; top: 170px; width: 300px;
    text-align: center; color: var(--ink-black);
    font-weight: 700; font-size: 23px; line-height: 1.15; letter-spacing: 2px;
    text-transform: uppercase;
  }

  .person { position: absolute; left: 387px; top: 92px; color: var(--ink-white); }
  .person-name { font-weight: 700; font-size: 21px; letter-spacing: 0.2px; }
  .person-title { font-size: 15px; color: var(--ink-soft); margin-top: 2px; }

  .address {
    position: absolute; left: 387px; top: 208px;
    color: var(--ink-soft); font-size: 16px; line-height: 22px;
  }

  .contact-bar {
    position: absolute; left: 385px; top: 273px; width: 22px; height: 111px;
    background: var(--icon-bar); border-radius: 4px;
  }
  .contacts {
    position: absolute; left: 385px; top: 273px; list-style: none;
    color: var(--ink-white); font-size: 16px;
  }
  .contacts li { display: flex; align-items: center; height: 27.75px; }
  .contacts svg { width: 22px; height: 14px; flex: none; margin-right: 21px; }

  .back-name {
    position: absolute; left: 0; right: 0; top: 178px;
    text-align: center; color: var(--back-mark);
    font-weight: 700; font-size: 42px; letter-spacing: 3px; text-transform: uppercase;
  }
</style>
</head>
<body>

<section class="card card-front" aria-label="Business card front">
  <svg class="front-panels" viewBox="0 0 725 414" width="725" height="414" aria-hidden="true">
    <polygon points="276,0 725,0 725,177 359,177" fill="var(--panel-grey)"/>
    <polygon points="362,190 725,190 725,414 276,414" fill="var(--panel-grey)"/>
  </svg>

  <div class="brand-name">Coastal Tundrabridge<br>Advisory</div>

  <div class="person">
    <div class="person-name">MATTHIAS KORHONEN, PHD</div>
    <div class="person-title">Founder &amp; Director</div>
  </div>

  <div class="address">PO Box 418259<br>Quillwater, Alaska 99642</div>

  <div class="contact-bar" aria-hidden="true"></div>
  <ul class="contacts">
    <li>
      <svg viewBox="0 0 22 14" aria-hidden="true"><path d="M7.5 3.5c.6-.6 1.2-.4 1.5 0l1 1.3c.3.4.2.8-.1 1.1l-.6.5c.5 1 1.1 1.6 2 2.1l.6-.6c.3-.3.7-.4 1.1-.1l1.3 1c.4.3.5.9 0 1.4-.8.9-1.8 1-3 .3-1.9-1.1-3.2-2.6-4-4.4-.4-1-.3-1.9.2-2.6z" fill="#fff"/></svg>
      +1-907-555-0143
    </li>
    <li>
      <svg viewBox="0 0 22 14" aria-hidden="true"><rect x="8.5" y="2.5" width="5" height="9" rx="1" fill="none" stroke="#fff" stroke-width="1.2"/></svg>
      (907) 555 0143
    </li>
    <li>
      <svg viewBox="0 0 22 14" aria-hidden="true"><rect x="7" y="4" width="8" height="6" fill="#fff"/><path d="M7 4l4 3.2L15 4" fill="none" stroke="var(--icon-bar)" stroke-width="1"/></svg>
      mkorhonen@tundrabridgeadvisory.example
    </li>
    <li>
      <svg viewBox="0 0 22 14" aria-hidden="true"><circle cx="11" cy="7" r="4.3" fill="none" stroke="#fff" stroke-width="1.1"/><ellipse cx="11" cy="7" rx="1.8" ry="4.3" fill="none" stroke="#fff" stroke-width="0.9"/><line x1="6.7" y1="7" x2="15.3" y2="7" stroke="#fff" stroke-width="0.9"/></svg>
      www.coastaltundrabridgeadvisory.example
    </li>
  </ul>
</section>

<section class="card card-back" aria-label="Business card back">
  <div class="back-name">Coastal Tundrabridge Advisory</div>
</section>

</body>
</html>
```